NexaBRIDGE new era @ Hyper Digitalization

We need a Brochure that show all our product, services and consulting related to Hyper Digitalization into the industrial internet of things world.
We need a document that can be handled as a electronic brochure, this means that we need to show strong corporate presence, with strong skill of technology, and we have credentials and key sucess projects related to Manufacturing industries.
Key industries that we attend: Automotive, Chemical, Food and Beverage, Mining, Paper and Pulp, Oil and Gas, Energy Management.
We save money to our customer in 6 ways: 1) Eficiency in operation 2) Production Control 3) Hyper Digitalization of Thing Optimizing asset ussage 4) Maintenance and predictive of assets risks 5) Quality Control reducing Cost 6) Augmented Reality in operation and control
Target Market(s)
Manufacturing Industry. CEO of companies that has challenges of saving operation costs into plants of manufacturing.
Industry/Entity Type
Software
Other font styles liked:
- MONTSERRAT
Requirements
Must have
- Technology Enviroment, our logo, our expertise, simple message about what our company does and the DNA, infography of the company, cases of sucess, cases of savings $ using our tecnology and services, what we can do for the customer in a few words
Nice to have
- standarize our colors related to our presentation, futuristic, information related to Artificial Inteligence related to machinery
Should not have
- old version of technology,

```html
<!DOCTYPE html>
<html lang="en">
<head>
<meta charset="utf-8">
<title>NexaBRIDGE Brochure Spread</title>
<link rel="stylesheet" href="https://fonts.googleapis.com/css2?family=Montserrat:wght@400;500;700&display=swap">
<style>
  :root {
    --backdrop: #d8cfca;
    --ink-dark: #16192b;
    --ink-light: #ffffff;
    --brand-blue: #1b74b8;
    --body-deep: #6580b1;
    --body-light: #93b4dc;
    --top-blue: #80a7d3;
    --top-mist: #a9cfd6;
    --leaf: #8dc63f;
  }
  * { box-sizing: border-box; margin: 0; padding: 0; }
  html, body { width: 1200px; height: 833px; overflow: hidden; }
  body {
    background: var(--backdrop);
    font-family: "Montserrat", sans-serif;
    color: var(--ink-light);
    position: relative;
  }
  .spread {
    position: absolute;
    left: 60px; top: 34px;
    width: 1080px; height: 764px;
    display: flex;
    box-shadow: 0 6px 18px rgba(60,50,45,.25);
  }
  .page {
    position: relative;
    width: 540px; height: 764px;
    overflow: hidden;
  }
  .page-bg { position: absolute; inset: 0; width: 100%; height: 100%; }
  .page-art {
    position: absolute;
    left: 0; right: 0; top: 300px; height: 300px;
    background: linear-gradient(180deg, rgba(255,255,255,0) 0%, rgba(255,255,255,.07) 50%, rgba(255,255,255,0) 100%);
  }
  .brand {
    position: absolute;
    top: 34px;
    font-size: 17px;
    font-weight: 500;
    color: var(--brand-blue);
    letter-spacing: .3px;
  }
  .page-left .brand { left: 38px; }
  .page-right .brand { right: 38px; }
  .heading {
    position: absolute;
    font-weight: 500;
    font-size: 29px;
    line-height: 1.25;
    letter-spacing: .6px;
  }
  .heading .dark { color: var(--ink-dark); display: block; }
  .heading .light { color: var(--ink-light); display: block; }
  .accent-bar {
    position: absolute;
    height: 4px;
    background: linear-gradient(90deg, var(--top-blue), var(--leaf));
  }
  .copy {
    position: absolute;
    font-size: 14.5px;
    line-height: 1.38;
    letter-spacing: .4px;
  }
  .copy p + p { margin-top: 14px; }
  .columns {
    position: absolute;
    left: 38px; top: 388px;
    display: flex;
    font-size: 11.5px;
    line-height: 1.3;
    letter-spacing: .3px;
  }
  .col { padding: 0 10px; }
  .col + .col { border-left: 2px solid var(--ink-light); }
  .col:first-child { padding-left: 0; width: 168px; }
  .col-services { width: 170px; }
  .col-training { width: 162px; }
  .col h3 { font-size: 11.5px; font-weight: 700; margin-bottom: 6px; }
  .col .label { margin: 4px 0 4px; }
  .col ul { list-style: none; margin-bottom: 10px; }
  .col li { position: relative; padding-left: 11px; margin-bottom: 4px; }
  .col li::before {
    content: ""; position: absolute; left: 0; top: 5px;
    width: 5px; height: 5px; border-radius: 50%; background: var(--ink-light);
  }
  .col-hwsw li { margin-bottom: 1px; }
</style>
</head>
<body>
  <main class="spread">
    <section class="page page-left">
      <svg class="page-bg" viewBox="0 0 540 764" preserveAspectRatio="none" aria-hidden="true">
        <defs>
          <linearGradient id="leftTop" x1="0" y1="0" x2="1" y2="0">
            <stop offset="0" stop-color="#7da3cf"/>
            <stop offset=".6" stop-color="#a9cfd6"/>
            <stop offset=".88" stop-color="#b8dc92"/>
            <stop offset="1" stop-color="#8dc63f"/>
          </linearGradient>
          <linearGradient id="leftBody" x1="0" y1="0" x2="1" y2="1">
            <stop offset="0" stop-color="#6380b2"/>
            <stop offset=".55" stop-color="#7f9fcc"/>
            <stop offset="1" stop-color="#95b5dd"/>
          </linearGradient>
        </defs>
        <rect width="540" height="764" fill="url(#leftTop)"/>
        <path d="M0,150 C110,125 200,80 300,88 C380,95 410,150 460,172 C500,190 525,205 540,215 L540,764 L0,764 Z" fill="url(#leftBody)"/>
      </svg>
      <div class="page-art" role="img" aria-label="Faint industrial machinery and circuit line illustration"></div>

      <div class="brand">NexaBRIDGE</div>

      <h1 class="heading" style="left:38px; top:96px;">
        <span class="dark">Our Expertise,</span>
        <span class="light">Consulting Strategy</span>
      </h1>
      <div class="accent-bar" style="left:38px; top:134px; width:190px;"></div>

      <div class="copy" style="left:38px; top:190px; width:460px;">
        <p>We know that all customers are in different maturity level of digitalization.</p>
        <p>Our Strategy helps to start simple, low cost and produce big changes. We have a graphic that represents the levels, and we need to show into graph that we can help them to take positive path of optimization</p>
      </div>

      <div class="columns">
        <div class="col col-hwsw">
          <h3>Hardware &amp; Software for industrial operations</h3>
          <p class="label">Software representatives:</p>
          <ul>
            <li>Vantora</li>
            <li>KTX Linkware</li>
            <li>Emberton</li>
            <li>OPC Raylink</li>
            <li>PeakBit</li>
          </ul>
          <p class="label">Hardware representatives:</p>
          <ul>
            <li>GX Automation</li>
            <li>Emberton</li>
            <li>Avantrel Computers</li>
            <li>SDT Comm</li>
          </ul>
        </div>
        <div class="col col-services">
          <h3>Services</h3>
          <ul>
            <li>OT interconnectivity for operations</li>
            <li>HMI &amp; MES Support</li>
            <li>Digital Production Process Optimization</li>
            <li>Migration services</li>
            <li>PLC &amp; PAC Control System Support</li>
            <li>Annual Support &amp; Outsourcing plant Engineers</li>
          </ul>
        </div>
        <div class="col col-training">
          <h3>Training</h3>
          <ul>
            <li>Training center &amp; courses:</li>
            <li>Linkware OPC</li>
            <li>HMI SCADA Marvelware Intact</li>
            <li>GX iVIEW, Simplexa, Plant Suite</li>
            <li>PLC Programming</li>
            <li>IIOT Platforms</li>
            <li>Machine Learning Platforms</li>
          </ul>
        </div>
      </div>
    </section>

    <section class="page page-right">
      <svg class="page-bg" viewBox="0 0 540 764" preserveAspectRatio="none" aria-hidden="true">
        <defs>
          <linearGradient id="rightTop" x1="0" y1="0" x2="1" y2="0">
            <stop offset="0" stop-color="#7fb03f"/>
            <stop offset=".3" stop-color="#86b0c8"/>
            <stop offset="1" stop-color="#86acd8"/>
          </linearGradient>
          <linearGradient id="rightBody" x1="0" y1="0" x2="0" y2="1">
            <stop offset="0" stop-color="#6882b4"/>
            <stop offset=".6" stop-color="#6f8fc0"/>
            <stop offset="1" stop-color="#7ea2d0"/>
          </linearGradient>
        </defs>
        <rect width="540" height="764" fill="url(#rightTop)"/>
        <path d="M0,235 C40,222 62,160 100,132 C150,96 200,140 262,110 C340,72 440,72 540,42 L540,764 L0,764 Z" fill="url(#rightBody)"/>
      </svg>
      <div class="page-art" role="img" aria-label="Faint factory conveyor and gear line illustration"></div>

      <div class="brand">NexaBRIDGE</div>

      <h2 class="heading" style="left:40px; top:196px;">
        <span class="dark">Get to know us</span>
      </h2>
      <div class="accent-bar" style="left:40px; top:236px; width:170px;"></div>

      <div class="copy" style="left:40px; top:256px; width:460px;">
        <p>We offer high performance technology</p>
        <p>State of the art in techniques with Artificial Intelligence and prototypes for new ways of doing manufacturing</p>
        <p>We play the rol as an Architect for a Digital world into the shopfloor operation at Machine Levels</p>
      </div>
    </section>
  </main>
</body>
</html>
```